I require a set of preaching screens for our Easter weekend.

1. Good Friday Service Title: The Lantern
2. Easter Sunday Service Title Still Water
3. Message Title Screen Title Still Water
Overview
We need a set of clean, minimal screen graphics for 3 service sermon series called Still Water
All screens must be delivered at 1920x1080px (16:9), suitable for projection in a church auditorium.

Design style
Minimal and clean. Uncluttered. Strong typography. Subtle use of imagery or texture — nothing busy or overly decorative.

The tone should feel thoughtful and weighty without being dark or heavy.

Subtitle: Letters Along a Quiet Mountain Road
Date range: 1 March – 5 April

Branding
No existing branding to match. Designer has creative freedom on colour palette and typography, provided the overall feel remains minimal and clean.
What to avoid
Busy backgrounds or heavy textures
All files in PNG at 1920x1080px
Editable source files (PSD or AI)

Please use images below as you feel is appropriate - we have permission for these - We want to see a at least three options for these screens to .

We need designs within 3 days

```html
<!DOCTYPE html>
<html lang="en">
<head>
<meta charset="utf-8">
<title>The Lantern — Good Friday Service</title>
<link rel="stylesheet" href="https://fonts.googleapis.com/css2?family=Newsreader:opsz,wght@6..72,400;6..72,500&display=swap">
<style>
  :root {
    --sky-top: #4a3a2e;
    --sky-glow: #b97a38;
    --sky-mid: #8f6132;
    --ridge: #6a4a2c;
    --haze-low: #3a2f28;
    --ground: #111820;
    --ground-deep: #08111b;
    --title-gold: #f7d77c;
    --mark-gold: #f6c467;
  }
  * { margin: 0; padding: 0; box-sizing: border-box; }
  html, body {
    width: 1200px;
    height: 675px;
    overflow: hidden;
    background: var(--ground-deep);
  }
  .screen {
    position: relative;
    width: 1200px;
    height: 675px;
    overflow: hidden;
    font-family: "Newsreader", Georgia, serif;
  }
  .backdrop {
    position: absolute;
    inset: 0;
    background:
      radial-gradient(ellipse 45% 22% at 30% 40%, rgba(214,140,60,0.55), rgba(214,140,60,0) 70%),
      linear-gradient(180deg,
        var(--sky-top) 0%,
        #6a4b30 18%,
        var(--sky-mid) 32%,
        var(--sky-glow) 42%,
        var(--ridge) 52%,
        #5b402a 60%,
        var(--haze-low) 70%,
        var(--ground) 76%,
        var(--ground-deep) 100%);
  }
  .corner-title {
    position: absolute;
    top: 20px;
    font-size: 35px;
    font-weight: 400;
    line-height: 1.2;
    color: var(--title-gold);
    letter-spacing: 0.2px;
  }
  .corner-title--series { left: 29px; }
  .corner-title--service { right: 25px; }
  .series-name {
    position: absolute;
    left: 0;
    right: 0;
    top: 338px;
    transform: translateY(-50%);
    text-align: center;
    font-size: 112px;
    font-weight: 500;
    line-height: 0.95;
    letter-spacing: -1px;
    color: var(--mark-gold);
  }
  .series-name span { display: block; }
</style>
</head>
<body>
  <main class="screen">
    <div class="backdrop" role="img" aria-label="Hazy sunset over distant mountain ridges"></div>

    <h1 class="corner-title corner-title--series">The Lantern</h1>
    <p class="corner-title corner-title--service">Good Friday Service</p>

    <p class="series-name"><span>Still</span><span>Water</span></p>
  </main>
</body>
</html>
```